Dorvik Electric Ltd

Looking for a single page website and Facebook page design. I am an electrical contractor based on Vancouver Island. I do service, custom homes, residential and commercial installations. My company just started out, so I don't have any pictures of installs yet. I have 25 years experience. I would like the colors to be my logo colors black and I have a black Brandt Halvard that will be my vehicle which I will have a wrap for.
Updates

I just posted the contest today, not sure why the deadline is the same day.

Industry/Entity Type

Electrician

Requirements
Must have
• Services provided, About me section, quote section,
Nice to have
• I am not quite sure yet, I need to see some designs first .

```html
<!DOCTYPE html>
<html lang="en">
<head>
<meta charset="utf-8">
<title>Dorvik Electric Ltd</title>
<link rel="stylesheet" href="https://fonts.googleapis.com/css2?family=Oswald:wght@500;600&family=Open+Sans:ital,wght@0,400;0,600;0,700;0,800;1,800&family=Cinzel:wght@500;700&display=swap">
<style>
  :root {
    --yellow: #f5b80f;
    --black: #0b0b0b;
    --charcoal: #1a1a1a;
    --white: #ffffff;
    --ink: #111111;
    --grey-text: #d8d8d8;
  }
  * { box-sizing: border-box; margin: 0; padding: 0; }
  html, body { width: 1200px; height: 2848px; overflow: hidden; background: var(--white); }
  body { font-family: "Open Sans", Arial, sans-serif; color: var(--ink); }
  .page { width: 1200px; height: 2848px; display: flex; flex-direction: column; }

  /* Hero */
  .hero { position: relative; height: 934px; overflow: hidden; color: var(--white); }
  .hero-photo { position: absolute; inset: 0;
    background: radial-gradient(ellipse at 72% 38%, #6a625a 0%, #3a3631 30%, #1c1a18 62%, #0d0c0b 100%); }
  .hero-shade { position: absolute; inset: 0; background: linear-gradient(90deg, rgba(0,0,0,.55) 0%, rgba(0,0,0,.15) 60%, rgba(0,0,0,.3) 100%); }
  .site-nav { position: relative; display: flex; align-items: center; padding: 60px 70px 0; }
  .brand { display: flex; align-items: center; gap: 14px; font-family: "Cinzel", serif; font-weight: 700; font-size: 17px; letter-spacing: 1px; }
  .brand-dot { width: 44px; height: 44px; border-radius: 50%; background: var(--yellow); }
  .menu { display: flex; gap: 48px; margin-left: 190px; font-family: "Cinzel", serif; font-weight: 700; font-size: 19px; letter-spacing: 2px; }
  .menu .active { background: var(--yellow); color: var(--black); padding: 3px 14px; border-radius: 3px; }
  .search { margin-left: auto; display: flex; align-items: center; gap: 8px; border: 1px solid var(--white); padding: 4px 12px; width: 150px; font-family: "Cinzel", serif; font-size: 14px; letter-spacing: 3px; }
  .hero-copy { position: relative; margin: 360px 0 0 70px; width: 900px; }
  .hero-title { font-family: "Oswald", sans-serif; font-weight: 600; font-size: 62px; line-height: 1.05; text-transform: uppercase; }
  .hero-title .accent { color: var(--yellow); }
  .hero-text { margin-top: 20px; font-size: 17px; line-height: 1.5; color: var(--grey-text); width: 860px; }
  .btn { display: inline-block; border-radius: 30px; font-weight: 800; text-transform: uppercase; letter-spacing: .5px; }
  .btn-yellow { background: var(--yellow); color: var(--black); }
  .btn-hero { margin-top: 26px; padding: 9px 26px; font-size: 15px; }

  /* Services */
  .services { height: 514px; background: var(--black); display: flex; justify-content: center; gap: 44px; padding-top: 50px; }
  .service-card { position: relative; width: 326px; height: 414px; border: 2px solid var(--yellow); border-radius: 36px; padding: 60px 28px 0; text-align: center; color: var(--white); }
  .service-icon { position: absolute; top: -20px; left: 50%; transform: translateX(-50%); background: var(--black); padding: 0 8px; }
  .service-title { position: absolute; top: 22px; left: 50%; transform: translateX(-50%); font-weight: 800; font-size: 19px; letter-spacing: 1px; color: var(--yellow); text-transform: uppercase; }
  .service-text { font-size: 14px; line-height: 1.55; margin-top: 26px; }
  .service-note { font-size: 14px; line-height: 1.55; margin-top: 14px; }
  .btn-small { margin-top: 24px; padding: 4px 18px; font-size: 12px; background: var(--white); color: var(--black); }

  /* Why */
  .why { height: 327px; border-top: 4px solid var(--yellow); border-bottom: 4px solid var(--yellow); text-align: center; padding: 34px 70px 0; }
  .why-title { font-weight: 600; font-size: 44px; }
  .why-text { margin-top: 16px; font-size: 15px; line-height: 1.55; }
  .btn-estimate { margin-top: 22px; padding: 8px 34px; font-size: 17px; font-style: italic; border: 2px solid var(--black); }

  /* About */
  .about { position: relative; height: 583px; color: var(--white); overflow: hidden; }
  .about-photo { position: absolute; inset: 0; background: linear-gradient(120deg, #141210 0%, #2b2620 45%, #403a30 70%, #1d1a16 100%); }
  .about-inner { position: relative; display: flex; padding: 50px 70px 0; }
  .about-copy { width: 520px; }
  .about-title { font-weight: 800; font-size: 54px; color: var(--yellow); }
  .about-text { margin-top: 14px; font-size: 16px; line-height: 1.6; }
  .btn-about { margin-top: 22px; padding: 5px 20px; font-size: 13px; }
  .about-gallery { margin-left: auto; display: grid; grid-template-columns: repeat(3, 150px); gap: 40px 36px; margin-top: 20px; }
  .gallery-item { width: 150px; height: 150px; border-radius: 50%; border: 6px solid var(--yellow); }
  .g1 { background: linear-gradient(135deg, #8a8f96, #3c4046); }
  .g2 { background: linear-gradient(135deg, #c7cbd0, #5a6a7c); }
  .g3 { background: linear-gradient(135deg, #d98a5a, #8c3a2a); }
  .g4 { background: linear-gradient(135deg, #e6d7b0, #9a8a62); }
  .g5 { background: linear-gradient(135deg, #b0a48c, #5d5446); }
  .g6 { background: linear-gradient(135deg, #e0b28c, #9a6440); }

  /* Estimate band */
  .estimate { height: 327px; background: var(--yellow); text-align: center; padding: 36px 70px 0; }
  .estimate-text { font-size: 15px; line-height: 1.55; color: var(--black); }
  .btn-dark { margin-top: 22px; padding: 9px 40px; font-size: 17px; font-style: italic; background: var(--black); color: var(--white); }
  .estimate-brand { margin-top: 34px; display: inline-flex; align-items: center; gap: 12px; font-family: "Cinzel", serif; font-weight: 700; font-size: 18px; color: var(--black); }
  .estimate-brand .brand-dot { width: 38px; height: 38px; background: var(--black); }

  /* Footer */
  .site-footer { height: 163px; text-align: center; padding-top: 30px; font-family: "Cinzel", serif; }
  .footer-menu { display: flex; justify-content: center; gap: 70px; font-weight: 700; font-size: 20px; letter-spacing: 2px; }
  .footer-legal { margin-top: 16px; display: flex; justify-content: center; gap: 70px; font-weight: 700; font-size: 13px; letter-spacing: 1px; }
  .copyright { margin-top: 14px; font-size: 12px; letter-spacing: 1px; }
</style>
</head>
<body>
<div class="page">

  <header class="hero">
    <div class="hero-photo" role="img" aria-label="Photo of an electrician in a white hard hat working at an electrical panel"></div>
    <div class="hero-shade"></div>
    <nav class="site-nav">
      <div class="brand"><span class="brand-dot"></span>Dorvik Electric Ltd</div>
      <div class="menu">
        <span class="active">About Us</span>
        <span>Opportunity</span>
        <span>Why Dorvik</span>
        <span>Contact</span>
      </div>
      <div class="search">
        <svg width="14" height="14" viewBox="0 0 14 14"><circle cx="6" cy="6" r="4.5" fill="none" stroke="#fff" stroke-width="1.5"/><line x1="9.3" y1="9.3" x2="13" y2="13" stroke="#fff" stroke-width="1.5"/></svg>
        Search
      </div>
    </nav>
    <div class="hero-copy">
      <h1 class="hero-title">Electrical Services<br>Based on <span class="accent">Vancouver Island</span></h1>
      <p class="hero-text">Licensed electrical contractor with 25 years of experience serving homes and businesses across Vancouver Island. Safe, tidy and code-compliant work on every job, from a single outlet to a full custom build.</p>
      <span class="btn btn-yellow btn-hero">Our Service</span>
    </div>
  </header>

  <section class="services">
    <article class="service-card">
      <svg class="service-icon" width="56" height="40" viewBox="0 0 56 40"><path d="M28 4 L10 20 H15 V36 H41 V20 H46 Z" fill="#f5b80f"/></svg>
      <h2 class="service-title">Residential</h2>
      <p class="service-text">Wiring, panel upgrades, lighting and EV chargers for new and existing homes. We keep your family safe and your power reliable, with clear quotes and clean finished work.</p>
      <p class="service-note">Custom home builds welcome.</p>
      <span class="btn btn-small">Learn More</span>
    </article>
    <article class="service-card">
      <svg class="service-icon" width="56" height="40" viewBox="0 0 56 40"><rect x="12" y="12" width="32" height="24" rx="3" fill="#f5b80f"/><rect x="22" y="5" width="12" height="9" rx="2" fill="none" stroke="#f5b80f" stroke-width="3"/></svg>
      <h2 class="service-title">Commercial</h2>
      <p class="service-text">Installations for offices, shops and light industrial spaces. Planned around your hours to keep your business running, built to code and ready for inspection.</p>
      <p class="service-note">Tenant improvements and upgrades.</p>
      <span class="btn btn-small">Learn More</span>
    </article>
    <article class="service-card">
      <svg class="service-icon" width="56" height="40" viewBox="0 0 56 40"><circle cx="28" cy="20" r="15" fill="#f5b80f"/><path d="M21 27 L33 15 M30 12 L36 18" stroke="#0b0b0b" stroke-width="4" stroke-linecap="round"/></svg>
      <h2 class="service-title">Service</h2>
      <p class="service-text">Fast troubleshooting and repairs when something stops working. Breakers, outlets, fixtures and faults found and fixed by an experienced electrician.</p>
      <p class="service-note">Call for same week service.</p>
      <span class="btn btn-small">Learn More</span>
    </article>
  </section>

  <section class="why">
    <h2 class="why-title">Why Dorvik Services</h2>
    <p class="why-text">Dorvik Electric brings 25 years of hands-on trade experience to every project. We show up on time, explain the work in plain terms and stand behind every installation. As a new local company, each customer matters and every job is done as if it were our own home.</p>
    <p class="why-text">From service calls to custom homes, you get one trusted electrician from quote to final inspection.</p>
    <span class="btn btn-yellow btn-estimate">Schedule an Estimate</span>
  </section>

  <section class="about">
    <div class="about-photo" role="img" aria-label="Dark photo of electrical wiring and equipment"></div>
    <div class="about-inner">
      <div class="about-copy">
        <h2 class="about-title">About Us</h2>
        <p class="about-text">Founded by a journeyman electrician with 25 years in the trade, Dorvik Electric serves residential and commercial clients across Vancouver Island. Our work covers new builds, renovations, service upgrades and repairs.</p>
        <p class="about-text">We believe in honest pricing, clear communication and tidy job sites. Look for our black truck around the island.</p>
        <span class="btn btn-yellow btn-about">Learn More</span>
      </div>
      <div class="about-gallery">
        <div class="gallery-item g1" role="img" aria-label="Electrician working on a switchboard"></div>
        <div class="gallery-item g2" role="img" aria-label="Electrical panel and breakers"></div>
        <div class="gallery-item g3" role="img" aria-label="Hands connecting coloured wires"></div>
        <div class="gallery-item g4" role="img" aria-label="Electrician installing a light fixture"></div>
        <div class="gallery-item g5" role="img" aria-label="Electrician at work in a home"></div>
        <div class="gallery-item g6" role="img" aria-label="Hands testing an outlet"></div>
      </div>
    </div>
  </section>

  <section class="estimate">
    <p class="estimate-text">Ready to start your project? Tell us what you need and we will get back to you with a free, detailed estimate. No pressure, no hidden fees, just straight answers from a local electrician.</p>
    <p class="estimate-text">Serving Nanaimo, Victoria, Courtenay and everywhere between.</p>
    <span class="btn btn-dark">Schedule an Estimate</span>
    <div><span class="estimate-brand"><span class="brand-dot"></span>Dorvik Electric Ltd</span></div>
  </section>

  <footer class="site-footer">
    <nav class="footer-menu">
      <span>Home</span><span>About Us</span><span>Opportunity</span><span>Why Dorvik</span><span>Contact</span>
    </nav>
    <div class="footer-legal"><span>Privacy Policy</span><span>Terms and Conditions</span></div>
    <p class="copyright">Copyright © 2022 Dorvik Electric Ltd. Company Reg No 10482736</p>
  </footer>

</div>
</body>
</html>
```